single page with calendar booking ability

a single web page that has the ability to book calendar times and dates, also needs to be able to link to my other business social media seamlessly. I don't want to get multiple developers and or agency's involved, I want you the web designer to design it and make sure it's up and works as described
. The boats we work on are between 20 feet to 40 feet, bow riders , cabin cruisers, and center consoles. The brands that we work on include but are not limited to Velmora, Praxen, Dunby Vale, Lark mil, Quilvane, Brevik, Drelo, and many more. Winterization and shrink wrapping is completely different than graphic wrapping, we do not do graphic's wrapping. Also, only 5% of our business will be auto detailing, the rest will be boats on trailers. Please ensure that the calendar booking system is intergraded and not a surprise to me later

Target Market(s)

Lakes region New Hampshire

Industry/Entity Type

marine

Coding

Coded - Design and coding required

Number of Pages Required

1 page

Colors
0054AA
0677BA
7BADD7
CADEEF
E8F1F8
00AB8E
00BBA5
67D7C9
C6EFE9
E9F9F6
EE7325
F08F49
F5BC92
FAE3D3
FDF4ED

Requirements
Must have
• calendar booking capability
Nice to have
• Pictures of boats being shrink wrapped for the winter season, Nice before and after pictures of boats detailed, only 5% of our business is auto detailing
Should not have
• Large yachts, lots of sail boats as we only do a few, graphics wrapping.. we don't graphic wrap

```html
<!DOCTYPE html>
<html lang="en">
<head>
<meta charset="utf-8">
<title>Lakeshore Marine – Boat Care in the Lakes Region</title>
<link rel="stylesheet" href="https://fonts.googleapis.com/css2?family=Roboto:wght@400;500;700;900&display=swap">
<style>
:root{
  --red:#e3262c;
  --blue:#0a66c2;
  --blue-dark:#0054aa;
  --blue-soft:#cadeef;
  --ink:#111;
  --text:#333;
  --muted:#8a8a8a;
  --grey-bg:#f1f1f1;
  --footer:#222325;
  --white:#fff;
}
*{box-sizing:border-box;margin:0;padding:0}
html,body{width:1200px;height:3861px;overflow:hidden}
body{position:relative;font-family:"Roboto",Arial,sans-serif;color:var(--text);background:var(--white)}
.abs{position:absolute}
a{text-decoration:none;color:inherit}

/* header */
.site-header{position:absolute;left:0;top:0;width:1200px;height:106px;background:var(--white)}
.brand{position:absolute;left:97px;top:30px;display:flex;align-items:center;gap:10px;font-weight:900;font-size:26px;color:var(--red);letter-spacing:.5px}
.brand-dot{width:22px;height:22px;border-radius:50%;background:var(--blue-dark)}
.nav a{position:absolute;top:39px;font-size:15px;font-weight:700;color:var(--ink)}
.nav a.active{color:var(--red);font-weight:500}
.btn{display:inline-flex;align-items:center;gap:12px;background:var(--red);color:var(--white);font-weight:700;font-size:15px;letter-spacing:.3px;border-radius:3px;padding:0 18px;height:46px;box-shadow:0 3px 8px rgba(0,0,0,.18)}
.btn svg{width:15px;height:15px}
.contact-btn{position:absolute;left:968px;top:27px;height:40px;font-size:15px;padding:0 16px}

/* hero */
.hero{position:absolute;left:0;top:106px;width:1200px;height:566px;background:linear-gradient(160deg,#3e6f9a 0%,#2a5f8e 35%,#1f5b8f 60%,#17497a 100%)}
.hero-title{position:absolute;left:108px;top:180px;font-size:52px;font-weight:700;color:var(--white);letter-spacing:.5px;text-shadow:0 2px 6px rgba(0,0,0,.35)}
.hero-text{position:absolute;left:111px;top:248px;width:450px;font-size:12.5px;line-height:21px;color:var(--white)}
.hero .btn{position:absolute;left:110px;top:318px}
.arrow-circle{position:absolute;width:38px;height:38px;border-radius:50%;background:var(--white);display:flex;align-items:center;justify-content:center}

/* section headings */
.h2{font-size:40px;font-weight:700;color:var(--ink);letter-spacing:.3px}
.rule{width:44px;height:3px;background:var(--red);margin-top:12px}
.body-text{font-size:15px;line-height:25.7px;color:var(--text)}

/* photo placeholders */
.photo{position:absolute}
.frame{position:absolute;border:1.5px solid var(--red)}

/* calendar */
.calendar-section{position:absolute;left:0;top:1275px;width:1200px;height:549px;background:var(--grey-bg)}
.date-line{color:var(--blue-dark);font-weight:500;font-size:17px}
.calendar{position:absolute;left:556px;top:1358px;width:558px;height:384px;border:6px solid var(--blue-dark);background:var(--white);box-shadow:0 4px 10px rgba(0,0,0,.2)}
.cal-bar{height:26px;display:flex;justify-content:space-between;align-items:center;padding:0 12px;font-size:13px;color:#222}
.cal-bar span::after{content:"";display:inline-block;margin-left:10px;border:5px solid transparent;border-top-color:#222;vertical-align:-3px}
.cal-head{display:grid;grid-template-columns:repeat(7,1fr);background:var(--blue-soft);height:28px;align-items:center;text-align:center;font-size:14px;font-weight:500;color:#1a1a1a}
.cal-grid{display:grid;grid-template-columns:repeat(7,1fr);grid-auto-rows:60px;gap:4px;padding:4px}
.day{border:1px solid #d9d9d9;box-shadow:0 1px 3px rgba(0,0,0,.12);padding:5px 8px;font-size:13px;color:#222;position:relative}
.day small{display:block;text-align:center;font-size:7px;margin-top:8px;line-height:12px}
.day .booked{color:var(--red)}
.day .open{color:#00ab8e}
.day .na{color:#888}
.day.today{background:var(--blue-dark);color:var(--white)}
.day.today .open{color:var(--white)}

/* swot */
.swot{position:absolute;left:0;top:2432px;width:1200px;height:512px;background:linear-gradient(180deg,#0f5fb3,#0a5aa9)}
.swot-title{position:absolute;left:0;top:62px;width:1200px;text-align:center;color:var(--white)}
.swot-title .rule{margin:10px auto 0;background:var(--red)}
.swot-card{position:absolute;top:169px;width:228px;height:270px;background:var(--white);border-radius:3px;padding:18px 18px 0}
.swot-card h3{font-size:15px;font-weight:700;color:var(--ink);line-height:17px;margin-top:10px}
.swot-card .rule{width:30px;height:2px;margin-top:6px}
.swot-card p{font-size:13px;line-height:21px;color:var(--muted);margin-top:14px}
.read-more{display:inline-flex;align-items:center;gap:8px;margin-top:8px;color:var(--blue);font-size:13px;font-weight:700;text-decoration:underline}
.icon{width:54px;height:54px}

/* executive summary */
.exec-title{position:absolute;left:0;top:3020px;width:1200px;text-align:center}
.exec-title .rule{margin:8px auto 0}
.exec-card{position:absolute;top:3114px;width:308px;height:258px;background:var(--white);box-shadow:0 2px 10px rgba(0,0,0,.18);padding:8px}
.exec-card .photo{position:static;height:176px;border-bottom:4px solid #333}
.exec-card h4{text-align:center;font-size:21px;font-weight:700;color:var(--ink);margin-top:30px}
.exec-card.feature{background:var(--blue-dark)}
.exec-card.feature .photo{border-bottom:none;height:180px}
.exec-card.feature h4{color:var(--white);font-size:16px;line-height:22px;margin-top:20px}
.go{position:absolute;right:-4px;bottom:-4px;width:36px;height:36px;border-radius:50%;background:var(--blue);display:flex;align-items:center;justify-content:center;border:2px solid var(--white)}

/* footer */
.site-footer{position:absolute;left:0;top:3459px;width:1200px;height:402px;background:var(--footer);color:var(--white)}
.site-footer h5{font-size:15px;font-weight:700;letter-spacing:.3px}
.site-footer h5::after{content:"";display:block;width:56px;height:2px;background:var(--white);margin-top:10px}
.links{list-style:none;margin-top:22px}
.links li{font-size:15px;height:38.5px}
.links li::before{content:"»";margin-right:12px}
.social{display:flex;gap:11px}
.social span{width:28px;height:28px;border-radius:50%;border:1.5px solid var(--white);display:block}
.contact-row{display:flex;gap:14px;align-items:flex-start;margin-top:22px}
.contact-row .ic{width:34px;height:34px;border-radius:50%;background:var(--white);flex:none;display:flex;align-items:center;justify-content:center}
.contact-row b{font-size:11.5px;font-weight:700;display:block;margin-bottom:4px}
.contact-row div{font-size:14px;line-height:21px}
.copyright{position:absolute;left:111px;top:346px;width:980px;border-top:1px solid #555;text-align:center;padding-top:14px;font-size:15px}
</style>
</head>
<body>

<header class="site-header">
  <div class="brand"><span class="brand-dot"></span>LAKESHORE</div>
  <nav class="nav">
    <a class="active" style="left:283px">HOME</a>
    <a style="left:367px">ABOUT US</a>
    <a style="left:487px">WHAT WE DO</a>
    <a style="left:627px">CALENDAR</a>
    <a style="left:752px">SWOT ANALYSIS</a>
    <svg class="abs" style="left:916px;top:40px" width="16" height="16" viewBox="0 0 16 16"><circle cx="6.5" cy="6.5" r="4.5" fill="none" stroke="#111" stroke-width="2"/><line x1="10" y1="10" x2="14" y2="14" stroke="#111" stroke-width="2.4"/></svg>
  </nav>
  <a class="btn contact-btn">CONTACT US</a>
</header>

<section class="hero" role="img" aria-label="Center console boat with outboard motors cruising over blue water">
  <h1 class="hero-title">LAKESHORE MARINE</h1>
  <p class="hero-text">We aim to run a company focused on providing customers in the lakes region of the central New Hampshire with a broad range of boats and cars services</p>
  <a class="btn">GET STARTED <svg viewBox="0 0 16 16"><circle cx="8" cy="8" r="7.5" fill="#fff"/><path d="M6.5 4.5 10 8l-3.5 3.5" fill="none" stroke="#e3262c" stroke-width="2"/></svg></a>
  <div class="arrow-circle" style="left:35px;top:256px"><svg width="14" height="14" viewBox="0 0 14 14"><path d="M9 2 4 7l5 5" fill="none" stroke="#111" stroke-width="2"/></svg></div>
  <div class="arrow-circle" style="left:1124px;top:256px"><svg width="14" height="14" viewBox="0 0 14 14"><path d="M5 2l5 5-5 5" fill="none" stroke="#111" stroke-width="2"/></svg></div>
</section>

<section id="about">
  <div class="frame" style="left:142px;top:786px;width:379px;height:402px"></div>
  <div class="photo" style="left:124px;top:758px;width:379px;height:402px;background:linear-gradient(180deg,#7fa7c4 0%,#5a8fb8 12%,#4f89b7 45%,#8da9b9 70%,#c9bda4 100%)" role="img" aria-label="Pickup truck launching a boat on a trailer at the lake shore"></div>
  <div class="abs" style="left:587px;top:780px;width:490px">
    <h2 class="h2">ABOUT US</h2>
    <div class="rule"></div>
    <p class="body-text" style="margin-top:28px">Lorem ipsum dolor sit amet, consectetur adipiscing elit, sed eiusmod tempor incididunt ut labore et dolore magna aliqua. Ut enim ad minim veniam, quis nostrud exercitation ullamco laboris nisi ut aliquip ex ea commodo consequat. Duis aute irure dolor in reprehenderit voluptate velit esse cillum dolore eu fugiat nulla pariatur. Excepteur sint occaecat cupidatat non proident, sunt in culpa qui officia deserunt mollit anim id est laborum.Sed ut perspiciatis unde omnis iste natus error luptatem accusantium doloremque laudantium, totam rem aperiam, eaque ipsa quae ab illo inventore veritatis.</p>
    <a class="btn" style="margin-top:34px">GET STARTED <svg viewBox="0 0 16 16"><circle cx="8" cy="8" r="7.5" fill="#fff"/><path d="M6.5 4.5 10 8l-3.5 3.5" fill="none" stroke="#e3262c" stroke-width="2"/></svg></a>
  </div>
</section>

<section class="calendar-section" id="calendar">
  <div class="abs" style="left:84px;top:113px;width:415px">
    <h2 class="h2">CALENDAR BOOKING</h2>
    <div class="rule"></div>
    <p class="date-line" style="margin-top:22px">September 10,2021</p>
    <p class="body-text" style="margin-top:16px">Lorem ipsum dolor sit amet, consectetur adipiscing elit, sed do eiusmod tempor incididunt ut labore et dolore magna aliqua. Ut enim ad minim veniam, quis nostrud exercitation ullamco laboris nisi ut aliquip ex ea commodo consequat. Duis aute irure dolor in reprehenderit in voluptate velit esse</p>
    <a class="btn" style="margin-top:26px;padding:0 22px">BOOK NOW <svg viewBox="0 0 16 16" style="margin-left:10px"><circle cx="8" cy="8" r="7.5" fill="#fff"/><path d="M6.5 4.5 10 8l-3.5 3.5" fill="none" stroke="#e3262c" stroke-width="2"/></svg></a>
  </div>
</section>

<div class="calendar">
  <div class="cal-bar"><span>September 2021</span><span>Month</span></div>
  <div class="cal-head"><div>SUN</div><div>MON</div><div>TUE</div><div>WED</div><div>THU</div><div>FRI</div><div>SAT</div></div>
  <div class="cal-grid">
    <div class="day"></div>
    <div class="day">1<small class="booked">Booked</small></div>
    <div class="day">2<small class="booked">Booked</small></div>
    <div class="day">3<small class="open">09.00am Available<br>02.00am Available</small></div>
    <div class="day">4<small class="booked">Booked</small></div>
    <div class="day">5<small class="open">09.00am Available<br>02.00am Available</small></div>
    <div class="day">6<small class="na">Not Available</small></div>

    <div class="day">7<small class="na">Not Available</small></div>
    <div class="day">8<small class="booked">Booked</small></div>
    <div class="day">9<small class="booked">Booked</small></div>
    <div class="day today">10<small class="open">09.00am Available<br>02.00am Available</small></div>
    <div class="day">11<small class="booked">Booked</small></div>
    <div class="day">12<small class="open">09.00am Available<br>02.00am Available</small></div>
    <div class="day">13<small class="na">Not Available</small></div>

    <div class="day">14<small class="na">Not Available</small></div>
    <div class="day">15<small class="booked">Booked</small></div>
    <div class="day">16<small class="booked">Booked</small></div>
    <div class="day">17<small class="open">09.00am Available<br>02.00am Available</small></div>
    <div class="day">18<small class="booked">Booked</small></div>
    <div class="day">19<small class="open">09.00am Available<br>02.00am Available</small></div>
    <div class="day">20<small class="na">Not Available</small></div>

    <div class="day">21<small class="na">Not Available</small></div>
    <div class="day">22<small class="booked">Booked</small></div>
    <div class="day">23<small class="booked">Booked</small></div>
    <div class="day">24<small class="open">09.00am Available<br>02.00am Available</small></div>
    <div class="day">25<small class="booked">Booked</small></div>
    <div class="day">26<small class="open">09.00am Available<br>02.00am Available</small></div>
    <div class="day">27<small class="na">Not Available</small></div>

    <div class="day">28<small class="na">Not Available</small></div>
    <div class="day">29</div>
    <div class="day">30</div>
    <div class="day"></div><div class="day"></div><div class="day"></div><div class="day"></div>
  </div>
</div>

<section id="what-we-do">
  <div class="abs" style="left:113px;top:1938px;width:500px">
    <h2 class="h2">WHAT WE DO</h2>
    <div class="rule"></div>
    <p class="body-text" style="margin-top:26px">We aim to run a company focused on providing customers in the lakes region of the central New Hampshire with a broad range of boats and cars services, including but not limited to shrink wrap for boats, mobile detailing for boats and cars, mobile winterization for boats and much more. We already own a company operating a floating bar and restaurant on Lake Winnipesaukee with a strong social media following and want to leverage on our existing audience to obtain hundreds of thousands of views and interactions every day to nurture positive word of mouth and organic advertising.</p>
    <a class="btn" style="margin-top:30px">GET STARTED <svg viewBox="0 0 16 16"><circle cx="8" cy="8" r="7.5" fill="#fff"/><path d="M6.5 4.5 10 8l-3.5 3.5" fill="none" stroke="#e3262c" stroke-width="2"/></svg></a>
  </div>
  <div class="frame" style="left:708px;top:1944px;width:379px;height:402px"></div>
  <div class="photo" style="left:690px;top:1916px;width:379px;height:402px;background:radial-gradient(ellipse at 55% 0%,#9fd2d6 0%,#3f8f9f 35%,#1f5f6e 70%,#163f4a 100%)" role="img" aria-label="Sea lion swimming under sunlit water"></div>
</section>

<section class="swot" id="swot">
  <div class="swot-title"><h2 class="h2" style="color:#fff">SWOT ANALYSIS</h2><div class="rule"></div></div>

  <article class="swot-card" style="left:117px">
    <svg class="icon" viewBox="0 0 54 54" fill="#0a66c2"><path d="M8 2l2 4 4 .5-3 3 .8 4L8 11.5 4.2 13.5 5 9.5 2 6.5 6 6z"/><path d="M25 2l2 4 4 .5-3 3 .8 4-3.8-2-3.8 2 .8-4-3-3 4-.5z"/><path d="M42 2l2 4 4 .5-3 3 .8 4-3.8-2-3.8 2 .8-4-3-3 4-.5z"/><circle cx="10" cy="27" r="5"/><circle cx="27" cy="25" r="6"/><circle cx="44" cy="27" r="5"/><path d="M2 44c0-7 4-10 8-10s8 3 8 10z"/><path d="M17 44c0-8 5-12 10-12s10 4 10 12z"/><path d="M36 44c0-7 4-10 8-10s8 3 8 10z"/></svg>
    <h3>FIRST CLASS CUSTOMER EXPERIENCE</h3><div class="rule"></div>
    <p>We offer a wide array of services to make a better customer experience, including shrink wrapping,</p>
    <a class="read-more">READ MORE <svg width="15" height="15" viewBox="0 0 16 16"><circle cx="8" cy="8" r="8" fill="#0a66c2"/><path d="M6.5 4.5 10 8l-3.5 3.5" fill="none" stroke="#fff" stroke-width="2"/></svg></a>
  </article>

  <article class="swot-card" style="left:363px">
    <svg class="icon" viewBox="0 0 54 54" fill="#0a66c2"><path d="M26 4v34H10z"/><path d="M29 10l14 28H29z"/><path d="M4 41h46l-6 10H10z"/></svg>
    <h3 style="margin-top:14px">CAPITAL INTENSIVE</h3><div class="rule"></div>
    <p>Our activity is capital intensive by definition and will require consistent upfront investment to develop a state-of-the-art</p>
    <a class="read-more">READ MORE <svg width="15" height="15" viewBox="0 0 16 16"><circle cx="8" cy="8" r="8" fill="#0a66c2"/><path d="M6.5 4.5 10 8l-3.5 3.5" fill="none" stroke="#fff" stroke-width="2"/></svg></a>
  </article>

  <article class="swot-card" style="left:610px">
    <svg class="icon" viewBox="0 0 54 54" fill="#0a66c2"><path d="M2 28h50l-6 10H8z"/><path d="M14 20h22l6 7H12z"/><rect x="18" y="22" width="4" height="3" fill="#fff"/><rect x="25" y="22" width="4" height="3" fill="#fff"/><path d="M2 42c6 3 10 3 16 0s10-3 16 0 12 3 18 0v3c-6 3-12 3-18 0s-10-3-16 0-10 3-16 0z"/></svg>
    <h3 style="margin-top:6px">GROWING MARKETS</h3><div class="rule"></div>
    <p>Big market potential with a solid and growing demand, with the opportunity to scale our growth and provide even</p>
    <a class="read-more">READ MORE <svg width="15" height="15" viewBox="0 0 16 16"><circle cx="8" cy="8" r="8" fill="#0a66c2"/><path d="M6.5 4.5 10 8l-3.5 3.5" fill="none" stroke="#fff" stroke-width="2"/></svg></a>
  </article>

  <article class="swot-card" style="left:855px">
    <svg class="icon" viewBox="0 0 54 54" fill="none" stroke="#0a66c2" stroke-width="3"><rect x="4" y="4" width="26" height="36" rx="2"/><circle cx="17" cy="18" r="7"/><circle cx="17" cy="18" r="2" fill="#0a66c2"/><line x1="9" y1="32" x2="25" y2="32"/><path d="M38 4v28c0 6 8 6 8 0V4"/><line x1="30" y1="40" x2="42" y2="40"/></svg>
    <h3 style="margin-top:14px">NEGATIVE EXTERNALITIES</h3><div class="rule"></div>
    <p>Externalities reducing the volume of customers, including lower spending power due to economic</p>
    <a class="read-more">READ MORE <svg width="15" height="15" viewBox="0 0 16 16"><circle cx="8" cy="8" r="8" fill="#0a66c2"/><path d="M6.5 4.5 10 8l-3.5 3.5" fill="none" stroke="#fff" stroke-width="2"/></svg></a>
  </article>
</section>

<section id="summary">
  <div class="exec-title"><h2 class="h2">EXECUTIVE SUMMARY</h2><div class="rule"></div></div>

  <article class="exec-card" style="left:110px">
    <div class="photo" style="background:linear-gradient(180deg,#5f8b4a 0%,#3f6d3a 25%,#2f6b7e 40%,#235d78 100%)" role="img" aria-label="Small motor boat on a green river"></div>
    <h4>Huge Market Potential</h4>
    <span class="go"><svg width="16" height="16" viewBox="0 0 16 16"><path d="M2 8h11M9 4l4 4-4 4" fill="none" stroke="#fff" stroke-width="2"/></svg></span>
  </article>

  <article class="exec-card feature" style="left:447px">
    <div class="photo" style="background:linear-gradient(180deg,#4f87c2 0%,#3b75b3 45%,#d7dde3 65%,#2b6aa8 80%,#1d5795 100%)" role="img" aria-label="Motor yacht moored near a rocky shore"></div>
    <h4>Attractive Investment<br>Prospect</h4>
    <span class="go"><svg width="16" height="16" viewBox="0 0 16 16"><path d="M2 8h11M9 4l4 4-4 4" fill="none" stroke="#fff" stroke-width="2"/></svg></span>
  </article>

  <article class="exec-card" style="left:783px">
    <div class="photo" style="background:linear-gradient(180deg,#c7d6e2 0%,#8aa6b7 30%,#4f7791 50%,#2f607f 100%)" role="img" aria-label="White motor cruiser on open water near a coastal town"></div>
    <h4>Solid Business Concept</h4>
    <span class="go"><svg width="16" height="16" viewBox="0 0 16 16"><path d="M2 8h11M9 4l4 4-4 4" fill="none" stroke="#fff" stroke-width="2"/></svg></span>
  </article>
</section>

<footer class="site-footer">
  <div class="abs" style="left:113px;top:62px;display:flex;align-items:center;gap:10px;font-weight:900;font-size:24px;color:var(--red)"><span class="brand-dot"></span>LAKESHORE</div>
  <p class="abs" style="left:112px;top:154px;width:280px;font-size:14px;line-height:21px">Lorem ipsum dolor sit amet, consectetur adipiscing elit, sed do eiusmod tempor</p>
  <p class="abs" style="left:111px;top:212px;font-size:15px;font-weight:700">FOLLOW US</p>
  <div class="abs social" style="left:111px;top:268px" aria-label="Social media links"><span></span><span></span><span></span><span></span></div>

  <div class="abs" style="left:472px;top:51px">
    <h5>QUICKLINKS</h5>
    <ul class="links"><li>Home</li><li>About Us</li><li>What We Do</li><li>Calendar</li><li>SWOT analysis</li></ul>
  </div>
  <div class="abs" style="left:681px;top:51px">
    <h5>OTHERLINKS</h5>
    <ul class="links"><li>FAR</li><li>Services</li><li>Team</li><li>Privacy</li><li>Policy</li></ul>
  </div>
  <div class="abs" style="left:869px;top:51px;width:230px">
    <h5>CONTACT US</h5>
    <div class="contact-row" style="margin-top:28px"><span class="ic"><svg width="16" height="16" viewBox="0 0 16 16"><path d="M3 1l3 3-1.5 2c1 2 3 4 5 5L11.5 9.5l3 3-2 2.5C6 14 2 10 .8 3z" fill="#222"/></svg></span><div><b>Phone Number :</b>123 (456) 789</div></div>
    <div class="contact-row"><span class="ic"><svg width="16" height="14" viewBox="0 0 16 14"><rect x="1" y="2" width="14" height="10" fill="none" stroke="#222" stroke-width="1.6"/><path d="M1 2l7 6 7-6" fill="none" stroke="#222" stroke-width="1.6"/></svg></span><div><b>Email:</b>hello@lakeshoremarine.com</div></div>
    <div class="contact-row"><span class="ic"><svg width="14" height="18" viewBox="0 0 14 18"><path d="M7 0C3 0 0 3 0 7c0 5 7 11 7 11s7-6 7-11c0-4-3-7-7-7z" fill="#222"/><circle cx="7" cy="7" r="2.5" fill="#fff"/></svg></span><div><b>Address :</b>716.Lorem ipsum dolor sit consectetur adipiscing elit</div></div>
  </div>

  <div class="copyright">©Copyrights 2021 Lakeshore Marine &nbsp; | &nbsp; All Rights Reserved &nbsp; |</div>
</footer>

</body>
</html>
```